Technology, Futuristic Innovation & Artificial Intelligence

I am looking for something with Artificial Intelligence DNA strands....
Blue, black, with white dna strands........I like clean, crisp, professional and not busy look.................................................................................................................................................................................................................................................................................................................................................................................. Thanks!

Target Market(s)

Engineers and United States Government Contractors

Industry/Entity Type

Engineering

Contact Information for Business Card

I've uploaded my logo the certification logo.

Font styles to use
Serif

Colors
3176b5
33a6d7
ffffff

Requirements
Must have
• Name
• Title
• Address
• Phone number
• website name
• certification logo
Nice to have
• Something with Artificial Intelligence DNA strands......
• **Please note it would be nice to have the business card 3D or textured with raised images. Thanks
Should not have
• Please no feminine flowery designs....this is an engineering firm

```html
<!DOCTYPE html>
<html lang="en">
<head>
<meta charset="utf-8">
<title>Novaris Business Card</title>
<link rel="stylesheet" href="https://fonts.googleapis.com/css2?family=Oswald:wght@400;500&family=Roboto+Condensed:wght@700&family=Work+Sans:wght@400&display=swap">
<style>
  :root {
    --page: #e8e6e2;
    --navy-deep: #070b1c;
    --navy: #121c52;
    --navy-glow: #1f3590;
    --cyan: #33a6d7;
    --blue: #3176b5;
    --black: #1b1c1e;
    --white: #ffffff;
    --silver: #d9dde3;
  }
  * { margin: 0; padding: 0; box-sizing: border-box; }
  html, body { width: 1200px; height: 930px; overflow: hidden; }
  body { background: var(--page); position: relative; font-family: "Work Sans", sans-serif; color: var(--white); }

  .card {
    position: absolute;
    left: 278px;
    width: 645px;
    height: 368px;
    border-radius: 22px;
    overflow: hidden;
    background: var(--navy-deep);
  }
  .card--front { top: 76px; }
  .card--back { top: 486px; }

  .circuit-field {
    position: absolute; inset: 0;
    background:
      radial-gradient(ellipse 60% 55% at 55% 40%, var(--navy-glow) 0%, transparent 70%),
      radial-gradient(ellipse 45% 40% at 85% 20%, #1a2a78 0%, transparent 70%),
      linear-gradient(90deg, var(--navy-deep) 0%, var(--navy) 45%, #16226a 100%);
  }

  .swoosh { position: absolute; inset: 0; width: 100%; height: 100%; }

  .naics {
    position: absolute; left: 32px; top: 26px;
    font-family: "Oswald", sans-serif; font-weight: 400;
    font-size: 21px; line-height: 30px; letter-spacing: -0.2px;
  }
  .naics-rule { position: absolute; left: 0; top: 47px; width: 32px; height: 1px; background: var(--silver); }
  .naics-rule::before { content: ""; position: absolute; left: 3px; top: -3px; width: 6px; height: 6px; border-radius: 50%; background: var(--silver); }

  .brand { position: absolute; }
  .brand-name {
    display: block;
    font-family: "Roboto Condensed", sans-serif; font-weight: 700;
    color: var(--silver); line-height: 1;
  }
  .brand-tagline {
    display: block; text-align: right;
    font-family: "Roboto Condensed", sans-serif; font-weight: 700; color: var(--white);
    letter-spacing: 0.3px;
  }

  .card--front .brand { left: 32px; top: 190px; width: 245px; }
  .card--front .brand-name { font-size: 40px; letter-spacing: 8px; }
  .card--front .brand-tagline { font-size: 10px; margin-top: 4px; }

  .card--back .brand { left: 134px; top: 184px; width: 380px; }
  .card--back .brand-name { font-size: 60px; letter-spacing: 14px; }
  .card--back .brand-tagline { font-size: 15px; margin-top: 4px; }

  .contact { position: absolute; right: 29px; top: 193px; text-align: right; }
  .contact-name { font-size: 24px; letter-spacing: 1px; line-height: 1.1; }
  .contact-title { font-size: 15px; margin-top: 3px; }
  .contact-address { font-size: 15.5px; line-height: 20px; margin-top: 11px; letter-spacing: 0.4px; }
  .contact-lines { list-style: none; margin-top: 6px; font-size: 15.5px; line-height: 20px; letter-spacing: 0.3px; }
  .contact-lines li { display: flex; justify-content: flex-end; align-items: center; gap: 10px; }
  .contact-lines svg { width: 9px; height: 9px; flex: none; }

  .vendor-seal { position: absolute; left: 301px; top: 268px; width: 80px; height: 80px; }
  .back-rule { position: absolute; left: 0; top: 47px; width: 160px; height: 2px; background: linear-gradient(90deg, var(--silver), transparent); }
</style>
</head>
<body>

<section class="card card--front" aria-label="Business card, front">
  <div class="circuit-field" role="img" aria-label="Glowing blue circuit board and star field background"></div>
  <svg class="swoosh" viewBox="0 0 806 460" preserveAspectRatio="none" aria-hidden="true">
    <path d="M0 340 C 170 400, 340 340, 520 255 C 640 200, 740 180, 806 205 L806 460 L0 460 Z" fill="var(--black)"/>
    <path d="M0 315 C 140 375, 290 360, 440 290 C 320 370, 140 390, 0 360 Z" fill="var(--blue)"/>
    <path d="M420 300 C 500 260, 570 230, 650 212 C 570 245, 500 275, 440 300 Z" fill="var(--cyan)" opacity="0.5"/>
    <path d="M40 400 C 220 410, 420 340, 600 230 C 700 175, 770 170, 806 190 C 760 180, 680 200, 600 245 C 430 350, 230 420, 40 400 Z" fill="#101113"/>
  </svg>

  <span class="naics-rule" aria-hidden="true"></span>
  <p class="naics">NAICS: 5413-10/30/40, 5416-11/14/18, 5419-90<br>5611-10, 5613--12/20/30, 5614-10</p>

  <div class="brand">
    <span class="brand-name">NOVARIS</span>
    <span class="brand-tagline">ENGINEERING WHAT COMES NEXT</span>
  </div>

  <div class="contact">
    <p class="contact-name">DANA WHITFIELD</p>
    <p class="contact-title">CEO</p>
    <p class="contact-address">1820 Marlowe Lane<br>Brookfield, SC 29000</p>
    <ul class="contact-lines">
      <li>555.010.4400
        <svg viewBox="0 0 10 10"><path d="M2 1 L4 1 L4.6 3 L3.4 3.8 C4 5.2 4.8 6 6.2 6.6 L7 5.4 L9 6 L9 8 C5 8.4 1.6 5 2 1 Z" fill="var(--blue)"/></svg>
      </li>
      <li>dwhitfield@novaris.org
        <svg viewBox="0 0 10 10"><rect x="0.7" y="2" width="8.6" height="6" fill="none" stroke="var(--blue)" stroke-width="1"/><path d="M0.7 2 L5 5.3 L9.3 2" fill="none" stroke="var(--blue)" stroke-width="1"/></svg>
      </li>
      <li>www.novaris.org
        <svg viewBox="0 0 10 10"><circle cx="5" cy="5" r="4.2" fill="none" stroke="var(--blue)" stroke-width="1"/><ellipse cx="5" cy="5" rx="1.8" ry="4.2" fill="none" stroke="var(--blue)" stroke-width="0.8"/><path d="M0.8 5 H9.2" stroke="var(--blue)" stroke-width="0.8"/></svg>
      </li>
    </ul>
  </div>
</section>

<section class="card card--back" aria-label="Business card, back">
  <div class="circuit-field" role="img" aria-label="Glowing blue circuit board and star field background"></div>
  <span class="back-rule" aria-hidden="true"></span>

  <div class="brand">
    <span class="brand-name">NOVARIS</span>
    <span class="brand-tagline">ENGINEERING WHAT COMES NEXT</span>
  </div>

  <svg class="vendor-seal" viewBox="0 0 80 80" role="img" aria-label="Verified vendor certification seal">
    <circle cx="40" cy="40" r="36" fill="var(--blue)" stroke="#c9a441" stroke-width="3"/>
  </svg>
</section>

</body>
</html>
```